web page look and feel - B2B enterprise application

We have an enterprise application with 10 to 15 core pages and several supporting pages or popups. To start, we want the graphical design of the Users, Roles and Data Source pages and their supporting popups, wizards, etc. to be made beautiful. That is around 10 pages in total. There is a fair amount of redundancy among the pages. I have attached 5 screenshots. We very much want the pages to project a premium feel. That is absolutely essential. The color scheme is blue and sometimes yellow (only if it makes the page look better) plus black, gray and white. If the design of these screens goes well, we would expand the project to continue with other pages. The core of what we are looking for is graphic in nature but we are open to workflow suggestions if you have them. The Roles screen needs some improvements to the layout. I am looking for everything that includes icons, fonts, spacing, etc. I assume getting to the final design will take some back and forth with multiple revisions.

Target Market(s)

Large Enterprises

Number of Pages Required

5+ page

Requirements
Must have
• Premium feel

```html
<!DOCTYPE html>
<html lang="en">
<head>
<meta charset="utf-8">
<title>Users – Corvell Data</title>
<link href="https://fonts.googleapis.com/css2?family=Lato:wght@400;700;900&display=swap" rel="stylesheet">
<style>
:root{
  --side:#232838;
  --side-dark:#1b1f2d;
  --blue:#2f6fae;
  --blue-nav:#3473b3;
  --row-alt:#e1ebf5;
  --line:#c9ccd2;
  --page:#f5f5f5;
  --yellow:#f7c12c;
  --green:#2cae45;
  --red:#e0262b;
  --ink:#222;
  --muted:#555;
}
*{box-sizing:border-box;margin:0;padding:0}
html,body{width:1200px;height:1130px;overflow:hidden}
body{font-family:'Lato',sans-serif;background:var(--page);color:var(--ink);position:relative}
.sidebar{position:absolute;left:0;top:0;width:274px;height:1130px;background:var(--side);color:#fff}
.brand{height:83px;display:flex;align-items:center;padding-left:36px;gap:12px;font-size:28px;font-weight:700}
.brand-dot{width:20px;height:20px;border-radius:50%;background:var(--yellow)}
.search{height:52px;background:var(--side-dark);display:flex;align-items:center;padding-left:42px;gap:14px;font-size:19px}
.adv{position:absolute;left:44px;top:145px;font-size:15px}
.nav{position:absolute;left:0;width:274px}
.nav-main{display:flex;align-items:center;height:42px;padding-left:32px;gap:20px;font-size:17px;font-weight:700}
.nav-main.active{background:var(--blue-nav)}
.nav-main svg{width:26px;height:22px;flex:none}
.nav-sub{font-size:15px;padding-left:96px;height:34px;line-height:34px}
.topbar{position:absolute;left:274px;top:0;right:0;height:83px;background:#fff;border-bottom:1px solid #ddd}
.tool{position:absolute;top:30px;width:24px;height:24px}
.menu-btn{position:absolute;left:633px;top:20px;width:43px;height:43px;border:2px solid #444;border-radius:50%;display:flex;align-items:center;justify-content:center}
.user-btn{position:absolute;left:697px;top:15px;width:129px;height:47px;border:2px solid var(--yellow);border-radius:24px;color:var(--yellow);font-weight:900;font-size:16px;display:flex;align-items:center;justify-content:center;gap:8px}
.title{position:absolute;left:310px;top:126px;font-size:40px;font-weight:900;letter-spacing:.5px}
.add-btn{position:absolute;left:448px;top:132px;width:61px;height:34px;background:var(--blue);color:#fff;font-weight:700;font-size:17px;display:flex;align-items:center;justify-content:center}
.grid{position:absolute;left:312px;width:790px;border:1px solid var(--line);background:#fff}
.row{display:flex;height:54px;border-bottom:1px solid var(--line)}
.row.alt{background:var(--row-alt)}
.row>div{display:flex;align-items:center;justify-content:center;border-right:1px solid var(--line);font-size:15px;color:#444;white-space:nowrap;overflow:hidden}
.row>div:last-child{border-right:none}
.head{background:var(--blue);height:55px}
.head>div{color:#fff !important;font-weight:700;font-size:17px !important;gap:6px;border-color:#4b82bb !important}
.c0{width:44px}.c1{width:125px}.c2{width:125px}.c3{width:119px}.c4{width:131px}.c5{width:125px}.c6{width:119px;gap:4px}
.ok{color:var(--green)!important;font-weight:700}
.off{color:var(--red)!important;font-weight:700}
.act{width:33px;height:33px;border:1.5px solid var(--blue);border-radius:50%;display:flex;align-items:center;justify-content:center}
.detail .drow{display:flex;height:51px;border-bottom:1px solid var(--line);font-size:16.5px;color:#555}
.detail .drow.alt{background:var(--row-alt)}
.drow>div{flex:1;display:flex;align-items:center;justify-content:center;gap:6px}
.drow>div:first-child{border-right:1px solid var(--line)}
.chk{width:15px;height:15px;background:var(--blue);border-radius:3px;display:inline-flex;align-items:center;justify-content:center;margin-left:8px}
.edit-area{height:78px;display:flex;align-items:center;justify-content:center}
.edit-btn{width:101px;height:45px;border-radius:23px;background:var(--yellow);color:#fff;font-weight:900;font-size:17px;display:flex;align-items:center;justify-content:center}
.pager{height:75px;display:flex;align-items:center;justify-content:center;gap:16px;color:#888}
.page-now{width:42px;height:29px;border-radius:15px;background:var(--yellow);color:#fff;font-weight:900;font-size:18px;display:flex;align-items:center;justify-content:center}
.size{width:66px;height:34px;border:1px solid #bbb;display:flex;align-items:center;justify-content:center;gap:10px;color:#333;font-size:15px;margin-left:12px}
.foot{position:absolute;left:274px;right:0;top:1071px;text-align:center;font-size:15px;color:#555}
</style>
</head>
<body>
<aside class="sidebar">
  <div class="brand"><span class="brand-dot"></span>Corvell Data</div>
  <div class="search">
    <svg width="20" height="20" viewBox="0 0 20 20"><circle cx="8" cy="8" r="6" fill="none" stroke="#fff" stroke-width="2.6"/><line x1="12.5" y1="12.5" x2="18" y2="18" stroke="#fff" stroke-width="2.8" stroke-linecap="round"/></svg>Search
  </div>
  <div class="adv">Advanced Search</div>

  <nav class="nav" style="top:219px">
    <div class="nav-main active"><svg viewBox="0 0 26 22"><path d="M2 18a11 11 0 0 1 22 0z" fill="#fff"/><circle cx="13" cy="13" r="2.5" fill="#3473b3"/><line x1="13" y1="13" x2="17" y2="8" stroke="#3473b3" stroke-width="2"/></svg>Users</div>
    <div class="nav-sub">Roles</div>
    <div class="nav-sub">Notification Groups</div>
  </nav>
  <nav class="nav" style="top:354px">
    <div class="nav-main"><svg viewBox="0 0 26 22"><ellipse cx="12" cy="4" rx="10" ry="3.5" fill="#fff"/><path d="M2 7c0 2 4.5 3.5 10 3.5S22 9 22 7v4c0 2-4.5 3.5-10 3.5S2 13 2 11zM2 14c0 2 4.5 3.5 10 3.5S22 16 22 14v4c0 2-4.5 3.5-10 3.5S2 20 2 18z" fill="#fff"/></svg>Data Sources</div>
    <div class="nav-sub">Data Object Relationships</div>
  </nav>
  <nav class="nav" style="top:454px">
    <div class="nav-main"><svg viewBox="0 0 26 22"><g fill="#fff"><rect x="1" y="2" width="6" height="5"/><rect x="9" y="2" width="7" height="5"/><rect x="18" y="2" width="7" height="5"/><rect x="1" y="9" width="6" height="5"/><rect x="9" y="9" width="7" height="5"/><rect x="18" y="9" width="7" height="5"/><rect x="1" y="16" width="6" height="5"/><rect x="9" y="16" width="7" height="5"/><rect x="18" y="16" width="7" height="5"/></g></svg>Data Sets</div>
  </nav>
  <nav class="nav" style="top:521px">
    <div class="nav-main"><svg viewBox="0 0 26 22"><g fill="#fff"><rect x="1" y="2" width="6" height="5"/><rect x="9" y="2" width="7" height="5"/><rect x="18" y="2" width="7" height="5"/><rect x="1" y="9" width="6" height="5"/><rect x="9" y="9" width="7" height="5"/><rect x="18" y="9" width="7" height="5"/><rect x="1" y="16" width="6" height="5"/><rect x="9" y="16" width="7" height="5"/><rect x="18" y="16" width="7" height="5"/></g></svg>Rule Sets</div>
  </nav>
  <nav class="nav" style="top:588px">
    <div class="nav-main"><svg viewBox="0 0 26 22"><circle cx="12" cy="11" r="9" fill="none" stroke="#fff" stroke-width="2.5"/><path d="M12 6v5h-4" fill="none" stroke="#fff" stroke-width="2.2"/></svg>Schedules</div>
  </nav>
  <nav class="nav" style="top:654px">
    <div class="nav-main"><svg viewBox="0 0 26 22"><path d="M3 14V7h16M15 3l5 4-5 4M23 8v7H7M11 19l-5-4 5-4" fill="none" stroke="#fff" stroke-width="2.6"/></svg>Metadata Import/Export</div>
    <div class="nav-sub">Import</div>
    <div class="nav-sub">Export</div>
  </nav>
</aside>

<header class="topbar">
  <svg class="tool" style="left:457px" viewBox="0 0 24 24"><path d="M1 19a11 11 0 0 1 22 0z" fill="#444"/><circle cx="12" cy="15" r="2" fill="#fff"/><line x1="12" y1="15" x2="16" y2="10" stroke="#fff" stroke-width="2"/><circle cx="6" cy="14" r="1.4" fill="#fff"/><circle cx="18" cy="14" r="1.4" fill="#fff"/></svg>
  <svg class="tool" style="left:504px" viewBox="0 0 24 24"><line x1="3" y1="21" x2="16" y2="8" stroke="#444" stroke-width="3.2" stroke-linecap="round"/><path d="M18 1l1 3 3 1-3 1-1 3-1-3-3-1 3-1z" fill="#444"/><circle cx="10" cy="4" r="1.2" fill="#444"/><circle cx="21" cy="13" r="1.2" fill="#444"/></svg>
  <svg class="tool" style="left:551px" viewBox="0 0 24 24"><circle cx="12" cy="12" r="10" fill="#444"/><path d="M9 9.5a3 3 0 1 1 4 2.8c-1 .4-1 1-1 2" fill="none" stroke="#fff" stroke-width="2.2"/><circle cx="12" cy="17.5" r="1.3" fill="#fff"/></svg>
  <svg class="tool" style="left:597px" viewBox="0 0 24 24"><g fill="#444"><circle cx="12" cy="12" r="7"/><rect x="10" y="1" width="4" height="22"/><rect x="1" y="10" width="22" height="4"/><rect x="10" y="1" width="4" height="22" transform="rotate(45 12 12)"/><rect x="10" y="1" width="4" height="22" transform="rotate(-45 12 12)"/></g><circle cx="12" cy="12" r="3" fill="#fff"/></svg>
  <div class="menu-btn"><svg width="20" height="16" viewBox="0 0 20 16"><g stroke="#444" stroke-width="2.6" stroke-linecap="round"><line x1="2" y1="2" x2="18" y2="2"/><line x1="2" y1="8" x2="18" y2="8"/><line x1="2" y1="14" x2="18" y2="14"/></g></svg></div>
  <div class="user-btn">DANA REYES <svg width="10" height="7" viewBox="0 0 10 7"><path d="M1 1l4 4 4-4" fill="none" stroke="#f7c12c" stroke-width="1.8"/></svg></div>
</header>

<h1 class="title">USERS</h1>
<div class="add-btn">ADD</div>

<section class="grid" style="top:211px">
  <div class="row head">
    <div class="c0"></div>
    <div class="c1">First Name <svg width="10" height="6"><path d="M0 0h10L5 6z" fill="#fff"/></svg></div>
    <div class="c2">Last Name <svg width="10" height="14"><path d="M0 6h10L5 0zM0 8h10l-5 6z" fill="#fff"/></svg></div>
    <div class="c3">User Name <svg width="10" height="14"><path d="M0 6h10L5 0zM0 8h10l-5 6z" fill="#fff"/></svg></div>
    <div class="c4">Email Address <svg width="10" height="14"><path d="M0 6h10L5 0zM0 8h10l-5 6z" fill="#fff"/></svg></div>
    <div class="c5">Status <svg width="10" height="14"><path d="M0 6h10L5 0zM0 8h10l-5 6z" fill="#fff"/></svg></div>
    <div class="c6"></div>
  </div>
  <div class="row">
    <div class="c0"><svg width="14" height="8"><path d="M1 1l6 6 6-6" fill="none" stroke="#555" stroke-width="1.6"/></svg></div>
    <div class="c1">Owen</div><div class="c2">Hale</div><div class="c3">owen.hale</div><div class="c4">owen@corvell.net</div><div class="c5 ok">Active</div>
    <div class="c6"><span class="act"><svg width="16" height="16" viewBox="0 0 16 16"><rect x="1.5" y="3" width="11" height="11" rx="2" fill="none" stroke="#2f6fae" stroke-width="1.5"/><path d="M6 10l1-3 7-7 2 2-7 7z" fill="#2f6fae"/></svg></span><span class="act"><svg width="16" height="16" viewBox="0 0 16 16"><rect x="1.5" y="4.5" width="8" height="10" rx="1.5" fill="none" stroke="#2f6fae" stroke-width="1.5"/><rect x="6" y="1.5" width="8" height="10" rx="1.5" fill="#fff" stroke="#2f6fae" stroke-width="1.5"/></svg></span><span class="act"><svg width="14" height="16" viewBox="0 0 14 16"><path d="M1 3.5h12M5 3V1.5h4V3M2.5 4l1 11h7l1-11M5.5 6.5v6M8.5 6.5v6" fill="none" stroke="#2f6fae" stroke-width="1.5"/></svg></span></div>
  </div>
  <div class="detail">
    <div class="drow"><div>Object</div><div>Permissions</div></div>
    <div class="drow alt"><div>System Settings</div><div><span class="chk"><svg width="10" height="8"><path d="M1 4l3 3 5-6" fill="none" stroke="#fff" stroke-width="2"/></svg></span>Read<span class="chk"><svg width="10" height="8"><path d="M1 4l3 3 5-6" fill="none" stroke="#fff" stroke-width="2"/></svg></span>Write</div></div>
    <div class="drow"><div>Users</div><div><span class="chk"><svg width="10" height="8"><path d="M1 4l3 3 5-6" fill="none" stroke="#fff" stroke-width="2"/></svg></span>Read<span class="chk"><svg width="10" height="8"><path d="M1 4l3 3 5-6" fill="none" stroke="#fff" stroke-width="2"/></svg></span>Write</div></div>
    <div class="drow alt"><div>Data Source</div><div>Role</div></div>
    <div class="drow"><div>All Data Sources</div><div>System Administrator</div></div>
    <div class="edit-area"><div class="edit-btn">EDIT</div></div>
  </div>
</section>

<section class="grid" style="top:682px">
  <div class="row">
    <div class="c0"><svg width="14" height="8"><path d="M1 1l6 6 6-6" fill="none" stroke="#555" stroke-width="1.6"/></svg></div>
    <div class="c1">Test</div><div class="c2">User</div><div class="c3">test.user</div><div class="c4">test@example.com</div><div class="c5 ok">Active</div>
    <div class="c6"><span class="act"><svg width="16" height="16" viewBox="0 0 16 16"><rect x="1.5" y="3" width="11" height="11" rx="2" fill="none" stroke="#2f6fae" stroke-width="1.5"/><path d="M6 10l1-3 7-7 2 2-7 7z" fill="#2f6fae"/></svg></span><span class="act"><svg width="16" height="16" viewBox="0 0 16 16"><rect x="1.5" y="4.5" width="8" height="10" rx="1.5" fill="none" stroke="#2f6fae" stroke-width="1.5"/><rect x="6" y="1.5" width="8" height="10" rx="1.5" fill="#fff" stroke="#2f6fae" stroke-width="1.5"/></svg></span><span class="act"><svg width="14" height="16" viewBox="0 0 14 16"><path d="M1 3.5h12M5 3V1.5h4V3M2.5 4l1 11h7l1-11M5.5 6.5v6M8.5 6.5v6" fill="none" stroke="#2f6fae" stroke-width="1.5"/></svg></span></div>
  </div>
  <div class="row alt">
    <div class="c0"><svg width="14" height="8"><path d="M1 1l6 6 6-6" fill="none" stroke="#555" stroke-width="1.6"/></svg></div>
    <div class="c1">Test</div><div class="c2">Test</div><div class="c3">test.test</div><div class="c4">test@example.com</div><div class="c5 ok">Active</div>
    <div class="c6"><span class="act"><svg width="16" height="16" viewBox="0 0 16 16"><rect x="1.5" y="3" width="11" height="11" rx="2" fill="none" stroke="#2f6fae" stroke-width="1.5"/><path d="M6 10l1-3 7-7 2 2-7 7z" fill="#2f6fae"/></svg></span><span class="act"><svg width="16" height="16" viewBox="0 0 16 16"><rect x="1.5" y="4.5" width="8" height="10" rx="1.5" fill="none" stroke="#2f6fae" stroke-width="1.5"/><rect x="6" y="1.5" width="8" height="10" rx="1.5" fill="#e1ebf5" stroke="#2f6fae" stroke-width="1.5"/></svg></span><span class="act"><svg width="14" height="16" viewBox="0 0 14 16"><path d="M1 3.5h12M5 3V1.5h4V3M2.5 4l1 11h7l1-11M5.5 6.5v6M8.5 6.5v6" fill="none" stroke="#2f6fae" stroke-width="1.5"/></svg></span></div>
  </div>
  <div class="row">
    <div class="c0"><svg width="14" height="8"><path d="M1 1l6 6 6-6" fill="none" stroke="#555" stroke-width="1.6"/></svg></div>
    <div class="c1">Lena</div><div class="c2">Voss</div><div class="c3">lena.voss</div><div class="c4">lena@corvell.com</div><div class="c5 off">In Active</div>
    <div class="c6"><span class="act"><svg width="16" height="16" viewBox="0 0 16 16"><rect x="1.5" y="3" width="11" height="11" rx="2" fill="none" stroke="#2f6fae" stroke-width="1.5"/><path d="M6 10l1-3 7-7 2 2-7 7z" fill="#2f6fae"/></svg></span><span class="act"><svg width="16" height="16" viewBox="0 0 16 16"><rect x="1.5" y="4.5" width="8" height="10" rx="1.5" fill="none" stroke="#2f6fae" stroke-width="1.5"/><rect x="6" y="1.5" width="8" height="10" rx="1.5" fill="#fff" stroke="#2f6fae" stroke-width="1.5"/></svg></span><span class="act"><svg width="14" height="16" viewBox="0 0 14 16"><path d="M1 3.5h12M5 3V1.5h4V3M2.5 4l1 11h7l1-11M5.5 6.5v6M8.5 6.5v6" fill="none" stroke="#2f6fae" stroke-width="1.5"/></svg></span></div>
  </div>
  <div class="row alt">
    <div class="c0"><svg width="14" height="8"><path d="M1 1l6 6 6-6" fill="none" stroke="#555" stroke-width="1.6"/></svg></div>
    <div class="c1">Dana</div><div class="c2">Reyes</div><div class="c3">dana.reyes</div><div class="c4">owen@corvell.net</div><div class="c5 ok">Active</div>
    <div class="c6"><span class="act"><svg width="16" height="16" viewBox="0 0 16 16"><rect x="1.5" y="3" width="11" height="11" rx="2" fill="none" stroke="#2f6fae" stroke-width="1.5"/><path d="M6 10l1-3 7-7 2 2-7 7z" fill="#2f6fae"/></svg></span><span class="act"><svg width="16" height="16" viewBox="0 0 16 16"><rect x="1.5" y="4.5" width="8" height="10" rx="1.5" fill="none" stroke="#2f6fae" stroke-width="1.5"/><rect x="6" y="1.5" width="8" height="10" rx="1.5" fill="#e1ebf5" stroke="#2f6fae" stroke-width="1.5"/></svg></span><span class="act"><svg width="14" height="16" viewBox="0 0 14 16"><path d="M1 3.5h12M5 3V1.5h4V3M2.5 4l1 11h7l1-11M5.5 6.5v6M8.5 6.5v6" fill="none" stroke="#2f6fae" stroke-width="1.5"/></svg></span></div>
  </div>
  <div class="row">
    <div class="c0"><svg width="14" height="8"><path d="M1 1l6 6 6-6" fill="none" stroke="#555" stroke-width="1.6"/></svg></div>
    <div class="c1">Milo</div><div class="c2">Grant</div><div class="c3">milo.grant</div><div class="c4">milo@mailbox.io</div><div class="c5 ok">Active</div>
    <div class="c6"><span class="act"><svg width="16" height="16" viewBox="0 0 16 16"><rect x="1.5" y="3" width="11" height="11" rx="2" fill="none" stroke="#2f6fae" stroke-width="1.5"/><path d="M6 10l1-3 7-7 2 2-7 7z" fill="#2f6fae"/></svg></span><span class="act"><svg width="16" height="16" viewBox="0 0 16 16"><rect x="1.5" y="4.5" width="8" height="10" rx="1.5" fill="none" stroke="#2f6fae" stroke-width="1.5"/><rect x="6" y="1.5" width="8" height="10" rx="1.5" fill="#fff" stroke="#2f6fae" stroke-width="1.5"/></svg></span><span class="act"><svg width="14" height="16" viewBox="0 0 14 16"><path d="M1 3.5h12M5 3V1.5h4V3M2.5 4l1 11h7l1-11M5.5 6.5v6M8.5 6.5v6" fill="none" stroke="#2f6fae" stroke-width="1.5"/></svg></span></div>
  </div>
  <div class="pager">
    <svg width="12" height="14"><rect x="0" y="0" width="2.5" height="14" fill="#888"/><path d="M12 0v14L3 7z" fill="#888"/></svg>
    <svg width="18" height="14"><rect x="0" y="0" width="2.5" height="14" fill="#888"/><path d="M10 0v14L3 7zM18 0v14L11 7z" fill="#888"/></svg>
    <div class="page-now">1</div>
    <svg width="18" height="14"><path d="M0 0v14l7-7zM8 0v14l7-7z" fill="#888"/><rect x="15.5" y="0" width="2.5" height="14" fill="#888"/></svg>
    <svg width="12" height="14"><path d="M0 0v14l9-7z" fill="#888"/><rect x="9.5" y="0" width="2.5" height="14" fill="#888"/></svg>
    <div class="size">20 <svg width="11" height="7"><path d="M1 1l4.5 4.5L10 1" fill="none" stroke="#333" stroke-width="1.6"/></svg></div>
  </div>
</section>

<footer class="foot">Copyright, 2018 © Corvell Data. All rights reserved.</footer>
</body>
</html>
```